Web design project for exciting Australian start-up

Background
We are looking for a creative and talented web design artist to work alongside our market leading web developer.
• You will be required to create a modern and clean design theme for our website, incorporating selected rustic colour scheme elements for our exciting Australian start-up to operate within the coffee industry.
reoccurring work to be expected to flow to the successful designer.
Requirements
• c. 5 - 10 page website
• Landing page
• Log in/ out
• 404 template
• Typography is emphasised
• Please use either a) typemarrow.com, b) free web fonts, c) brindle fonts
• All design elements in vector format
• Preferably with icons for each header title(i.e. about us, how it works etc) but designer have free reign over how the site looks, so might not be applicable
• All pages to be responsive
• Down to eSlab resolution

High level visual design brief attached - additional pages to be worked from base design.

Design inspiration
• We would like to use design elements from the following sources:
http://www.zandrix.com/halcyon/ (Functionality)
Colour scheme refer to logo and complementary style guide

```html
<!DOCTYPE html>
<html lang="en">
<head>
<meta charset="utf-8">
<title>Beanhaven – Australia's first online coffee marketplace</title>
<link rel="stylesheet" href="https://fonts.googleapis.com/css2?family=Mulish:wght@400;500;600;700;800&display=swap">
<style>
  :root {
    --orange: #f7964a;
    --charcoal: #3f4245;
    --red: #e8413f;
    --text-grey: #666666;
    --footer-bg: #f4f4f4;
    --bar-bg: #262626;
    --white: #ffffff;
    --ink: #2b2b2b;
    --brand-faint: #bdbdbd;
  }
  * { box-sizing: border-box; margin: 0; padding: 0; }
  html, body { width: 1200px; height: 919px; overflow: hidden; }
  body { font-family: "Mulish", sans-serif; background: var(--white); position: relative; }
  a { text-decoration: none; color: inherit; }

  .site-header { position: absolute; top: 0; left: 0; width: 1200px; height: 130px; background: var(--white); }
  .brand { position: absolute; left: 100px; top: 27px; height: 81px; display: flex; align-items: center; gap: 12px; }
  .brand-dot { width: 62px; height: 62px; border-radius: 50%; background: var(--orange); }
  .brand-name { font-size: 30px; font-weight: 800; color: var(--ink); letter-spacing: 1px; }
  .auth-nav { position: absolute; top: 49px; right: 99px; display: flex; gap: 19px; }
  .btn { display: inline-flex; align-items: center; justify-content: center; height: 31px; color: var(--white); font-size: 16px; font-weight: 600; }
  .btn-login { width: 81px; background: var(--orange); }
  .btn-signup { width: 81px; background: var(--charcoal); }

  .hero { position: absolute; top: 130px; left: 0; width: 1200px; height: 528px; overflow: hidden; }
  .hero-photo { position: absolute; inset: 0;
    background:
      radial-gradient(ellipse 300px 230px at 870px 300px, #7a3a1c 0%, #5c2a14 45%, rgba(92,42,20,0) 100%),
      radial-gradient(ellipse 420px 260px at 360px 460px, #4a2a1c 0%, rgba(74,42,28,0) 100%),
      linear-gradient(90deg, #c9b3a8 0%, #a88a7c 30%, #8a5a40 60%, #c0703a 100%); }
  .hero-title { position: absolute; left: 180px; top: 128px; width: 342px; text-align: center; color: var(--white); font-size: 38px; font-weight: 600; line-height: 56px; }
  .btn-video { position: absolute; left: 257px; top: 307px; width: 186px; height: 43px; background: var(--charcoal); color: var(--white); font-size: 18px; font-weight: 500; display: flex; align-items: center; justify-content: center; gap: 14px; }
  .slider-arrow { position: absolute; top: 252px; width: 48px; height: 48px; }
  .slider-prev { left: 54px; }
  .slider-next { left: 1101px; }

  .site-footer { position: absolute; top: 658px; left: 0; width: 1200px; height: 203px; background: var(--footer-bg); }
  .footer-col { position: absolute; top: 38px; }
  .footer-col h3 { font-size: 15px; font-weight: 700; color: var(--red); margin-bottom: 10px; }
  .footer-col li { list-style: none; font-size: 13px; color: var(--text-grey); line-height: 25px; }
  .col-info { left: 100px; }
  .col-about { left: 388px; top: 41px; }
  .col-contact { left: 656px; top: 41px; }
  .social-icons { display: flex; gap: 8px; margin-top: 4px; }
  .social-icons span { width: 28px; height: 28px; background: #555; display: block; border-radius: 3px; }
  .social-links { margin-top: 14px; font-size: 11px; color: var(--text-grey); }
  .footer-brand { position: absolute; left: 897px; top: 78px; display: flex; align-items: center; gap: 10px; }
  .footer-brand .brand-dot { width: 40px; height: 40px; background: #dcdcdc; }
  .footer-brand .brand-name { font-size: 22px; color: var(--brand-faint); }

  .legal-bar { position: absolute; top: 861px; left: 0; width: 1200px; height: 58px; background: var(--bar-bg); color: var(--white); font-size: 13px; font-weight: 600; display: flex; align-items: center; justify-content: center; padding-right: 20px; }
  .legal-bar .accent { color: var(--red); }
</style>
</head>
<body>
  <header class="site-header">
    <a class="brand" href="#"><span class="brand-dot"></span><span class="brand-name">BEANHAVEN</span></a>
    <nav class="auth-nav">
      <a class="btn btn-login" href="#">Login</a>
      <a class="btn btn-signup" href="#">Signup</a>
    </nav>
  </header>

  <section class="hero">
    <div class="hero-photo" role="img" aria-label="Steaming cup of coffee on a saucer beside scattered roasted coffee beans"></div>
    <h1 class="hero-title">Australia’s first online coffee marketplace</h1>
    <a class="btn-video" href="#">Watch Video
      <svg width="10" height="14" viewBox="0 0 10 14"><path d="M2 1.5 L8 7 L2 12.5" fill="none" stroke="#fff" stroke-width="2.6"/></svg>
    </a>
    <svg class="slider-arrow slider-prev" viewBox="0 0 48 48"><circle cx="24" cy="24" r="22.5" fill="none" stroke="var(--orange)" stroke-width="1.6"/><path d="M27 16 L19 24 L27 32" fill="none" stroke="var(--orange)" stroke-width="1.6"/></svg>
    <svg class="slider-arrow slider-next" viewBox="0 0 48 48"><circle cx="24" cy="24" r="22.5" fill="none" stroke="#fff" stroke-width="1.6"/><path d="M21 16 L29 24 L21 32" fill="none" stroke="#fff" stroke-width="1.6"/></svg>
  </section>

  <footer class="site-footer">
    <div class="footer-col col-info">
      <h3>Helpful info</h3>
      <ul><li>About us</li><li>Media enquiries</li><li>Terms &amp; conditions</li><li>Privacy policy</li></ul>
    </div>
    <div class="footer-col col-about">
      <h3>Who we are</h3>
      <ul><li>How it works</li><li>FAQ</li><li>Contact us</li></ul>
    </div>
    <div class="footer-col col-contact">
      <h3>Get In Touch</h3>
      <div class="social-icons"><span></span><span></span><span></span><span></span></div>
      <p class="social-links">Friendwall&nbsp; / &nbsp;Chirpline&nbsp; / &nbsp;Reelhub&nbsp; / &nbsp;Workring</p>
    </div>
    <div class="footer-brand"><span class="brand-dot"></span><span class="brand-name">BEANHAVEN</span></div>
  </footer>

  <div class="legal-bar">Copyright&nbsp;<span class="accent">Beanhaven</span>&nbsp;| Site Map | Contact Details | Privacy Policy</div>
</body>
</html>
```